Banner Design

We need a vinyl outside banner designed to be printed for Kelbrook Vale Residential Communities, based in Sydney. Our product is colleges and apartments for students. Our target market are students that are not currently living on campus and have long journeys. We need the message "You could be home right now" to be displayed. This would be displayed at bus stops where students are waiting in long lines to get home, when it's cold outside and they have a long journey ahead. The final design should be clear, concise and communicate the convenience of living on campus. Size is 3m wide by 1m high with 2 inch border around the design.

```html
<!DOCTYPE html>
<html lang="en">
<head>
<meta charset="utf-8">
<title>Kelbrook Vale Residential Communities – Bus Stop Banner</title>
<link rel="stylesheet" href="https://fonts.googleapis.com/css2?family=Source+Sans+3:wght@700&display=swap">
<style>
  :root {
    --banner-yellow: #fbd40a;
    --border-white: #ffffff;
    --ink: #231f20;
  }
  html, body {
    margin: 0;
    padding: 0;
    overflow: hidden;
    background: var(--border-white);
  }
  .banner {
    position: relative;
    width: 1200px;
    height: 400px;
    background: var(--border-white);
    box-sizing: border-box;
    padding: 10px;
    overflow: hidden;
  }
  .banner__field {
    position: relative;
    width: 100%;
    height: 100%;
    background: var(--banner-yellow);
  }
  .brand {
    position: absolute;
    left: 70px;
    top: 82px;
    width: 240px;
    display: flex;
    flex-direction: column;
    align-items: center;
    color: var(--ink);
    font-family: "Source Sans 3", "Helvetica Neue", Arial, sans-serif;
    font-weight: 700;
  }
  .brand__mark {
    display: block;
    width: 86px;
    height: 86px;
  }
  .brand__name {
    margin: 22px 0 0;
    font-size: 40px;
    line-height: 1;
    letter-spacing: 0.02em;
    text-align: center;
    text-transform: uppercase;
  }
  .headline {
    position: absolute;
    left: 406px;
    top: 128px;
    margin: 0;
    color: var(--ink);
    font-family: "Source Sans 3", "Helvetica Neue", Arial, sans-serif;
    font-weight: 700;
    font-size: 76px;
    line-height: 72px;
    letter-spacing: 0.01em;
    text-transform: uppercase;
  }
  .headline__line {
    display: block;
  }
</style>
</head>
<body>
  <main class="banner">
    <div class="banner__field">
      <div class="brand">
        <svg class="brand__mark" viewBox="0 0 86 86" aria-hidden="true">
          <rect x="0" y="0" width="86" height="86" fill="#231f20"/>
        </svg>
        <p class="brand__name">Kelbrook<br>Vale</p>
      </div>
      <h1 class="headline">
        <span class="headline__line">You could be</span>
        <span class="headline__line">home right now</span>
      </h1>
    </div>
  </main>
</body>
</html>
```